business card deign

Logo needs the following on it.
1. attached logo
2. Tagline - "If it chills the cooler or lights up the night...we build it!"
3. Name- Dalton Pikes, Founder and CPO
4. Address - 412 E. Carver Avenue, Ste 2207, Tampa, FL. 33917
5. Phone - 555.318.4726

```html
<!DOCTYPE html>
<html lang="en">
<head>
<meta charset="utf-8">
<title>Kelvo Business Card</title>
<link href="https://fonts.googleapis.com/css2?family=Roboto:wght@700;900&family=Open+Sans:wght@400;600&display=swap" rel="stylesheet">
<style>
  :root {
    --stage: #232323;
    --ink: #0d0d0d;
    --paper: #ffffff;
    --card-dark: #111111;
  }
  * { box-sizing: border-box; margin: 0; padding: 0; }
  html, body { width: 1200px; height: 711px; overflow: hidden; }
  body {
    background: var(--stage);
    display: flex;
    align-items: center;
    justify-content: center;
    gap: 40px;
    font-family: "Open Sans", sans-serif;
  }
  .card {
    position: relative;
    width: 540px;
    height: 308px;
    border-radius: 22px;
    overflow: hidden;
    box-shadow: 0 10px 30px rgba(0,0,0,0.5);
  }
  .card-front {
    background: var(--card-dark);
    display: flex;
    align-items: center;
    justify-content: center;
  }
  .brand {
    display: flex;
    align-items: center;
    gap: 14px;
    font-family: "Roboto", sans-serif;
    font-weight: 900;
    letter-spacing: 0.35em;
    text-transform: uppercase;
    white-space: nowrap;
  }
  .brand-mark { border-radius: 50%; flex: none; }
  .card-front .brand { color: var(--paper); font-size: 52px; }
  .card-front .brand-mark { width: 40px; height: 40px; background: var(--paper); }

  .card-back { background: var(--paper); color: var(--ink); }
  .card-back .brand {
    position: absolute;
    left: 34px;
    top: 92px;
    font-size: 30px;
    color: var(--ink);
  }
  .card-back .brand-mark { width: 24px; height: 24px; background: var(--ink); }
  .corner-tab {
    position: absolute;
    right: 0;
    top: 22px;
    width: 16px;
    height: 52px;
    background: var(--ink);
  }
  .person {
    position: absolute;
    right: 30px;
    top: 26px;
    text-align: right;
  }
  .person-name {
    font-family: "Roboto", sans-serif;
    font-weight: 900;
    font-size: 24px;
    line-height: 1.1;
  }
  .person-title { font-weight: 600; font-size: 13px; }
  .contact {
    position: absolute;
    right: 30px;
    top: 150px;
    list-style: none;
    text-align: right;
    font-size: 14px;
    line-height: 1.35;
  }
  .contact li { display: flex; justify-content: flex-end; align-items: flex-start; gap: 8px; }
  .contact svg { width: 13px; height: 13px; margin-top: 3px; flex: none; }
  .tagline {
    position: absolute;
    left: 34px;
    bottom: 30px;
    font-size: 14px;
    line-height: 1.35;
    width: 260px;
  }
</style>
</head>
<body>
  <section class="card card-front">
    <div class="brand"><span class="brand-mark"></span>Kelvo</div>
  </section>

  <section class="card card-back">
    <span class="corner-tab"></span>
    <div class="brand"><span class="brand-mark"></span>Kelvo</div>
    <div class="person">
      <p class="person-name">Dalton Pikes</p>
      <p class="person-title">Founder and CPO</p>
    </div>
    <ul class="contact">
      <li>555.318.4726
        <svg viewBox="0 0 24 24" aria-hidden="true"><path fill="currentColor" d="M6.6 10.8a15.1 15.1 0 0 0 6.6 6.6l2.2-2.2a1 1 0 0 1 1-.25 11.4 11.4 0 0 0 3.6.57 1 1 0 0 1 1 1V20a1 1 0 0 1-1 1A17 17 0 0 1 3 4a1 1 0 0 1 1-1h3.5a1 1 0 0 1 1 1c0 1.25.2 2.45.57 3.57a1 1 0 0 1-.25 1z"/></svg>
      </li>
      <li>412 E. Carver Avenue,<br>Ste 2207, Tampa, FL. 33917
        <svg viewBox="0 0 24 24" aria-hidden="true"><path fill="currentColor" d="M12 2a7 7 0 0 0-7 7c0 5.2 7 13 7 13s7-7.8 7-13a7 7 0 0 0-7-7zm0 9.5A2.5 2.5 0 1 1 12 6.5a2.5 2.5 0 0 1 0 5z"/></svg>
      </li>
    </ul>
    <p class="tagline">If it chills the cooler or<br>lights up the night...we build it!</p>
  </section>
</body>
</html>
```